Sophisticated, clean website reflecting my feminine, playful side to sell my abstract art,

I need a website no more than 3 pages to showcase my paintings, a little about me and some contact info. I do abstracts so looking for something a little edgy, yet feminine and current.
Updates

Hi there, These are some artists websites that I Iike: Marnelvoss.com (I like how airy it is) peterwallombry.com garethpolvens.com (I like how it scrolls) I'll need a place for a photo ( a headshot-i do not have it yet so I'll need to be able to upload that later) as well as an area for my bio. Also, it's important that I will be able to upload any new photos and descriptions easily so it should be user friendly. Lastly, I like in a sunny place so would like to have this seem upbeat and playful as that is how i like to paint. thanks-I'm trying to upload my photos now -

Target Market(s)

ppl ages 35-70 who want large scale art for their homes

Industry/Entity Type

art

Coding

Coded - Design and coding required

Number of Pages Required

3 page

Colors

Designer to choose colors to be used in the design.

Requirements
Must have
• photos of my art, a place for my bio, be easy to reach me. tasteful-nothing too "in your face" -my clients are pretty high end and organized. They like clean lines
Nice to have
• sophisticated background, muted tones in the back-similar clean font throughout-no cursive
Should not have
• too many dark areas. Too many blocks of color. Too serious.

```html
<!DOCTYPE html>
<html lang="en">
<head>
<meta charset="utf-8">
<title>Lydia Marrow – Abstract Art</title>
<link rel="stylesheet" href="https://fonts.googleapis.com/css2?family=Jost:wght@300;400&family=Quicksand:wght@400;500&display=swap">
<style>
  :root {
    --ink: #3b3b3b;
    --ink-soft: #555555;
    --rule: #9a9a9a;
    --mist: #e8e8e8;
    --shadow: #d6d6d6;
    --paper: #ffffff;
    --accent: #1a1a1a;
  }
  * { box-sizing: border-box; margin: 0; padding: 0; }
  html, body { width: 1200px; height: 2901px; overflow: hidden; background: var(--paper); }
  body { position: relative; font-family: "Quicksand", sans-serif; color: var(--ink); }

  .brand {
    position: absolute; top: 34px; left: 0; width: 1200px;
    display: flex; justify-content: center; align-items: center; gap: 16px;
    font-family: "Jost", sans-serif; font-weight: 300; font-size: 47px;
    letter-spacing: 1px; color: var(--ink-soft);
  }
  .brand-mark { width: 30px; height: 30px; background: var(--ink-soft); }
  .header-rule { position: absolute; top: 113px; left: 0; width: 1200px; height: 1px; background: var(--rule); }

  .main-nav { position: absolute; top: 131px; left: 0; width: 1200px; height: 24px;
    font-family: "Jost", sans-serif; font-size: 18px; color: var(--ink); }
  .main-nav a { position: absolute; color: inherit; text-decoration: none; transform: translateX(-50%); white-space: nowrap; }
  .nav-dot { position: absolute; top: 10px; width: 4px; height: 4px; background: var(--rule); }

  .hero { position: absolute; top: 173px; left: 0; width: 1200px; height: 681px;
    background:
      radial-gradient(ellipse at 30% 40%, rgba(46,150,90,.85), transparent 55%),
      radial-gradient(ellipse at 80% 65%, rgba(20,100,110,.8), transparent 50%),
      radial-gradient(ellipse at 55% 85%, rgba(190,120,30,.55), transparent 40%),
      linear-gradient(120deg, #d9e6dd 0%, #6fb36a 35%, #e8ecea 55%, #2f8a8a 80%, #6a5a4a 100%); }
  .arrow { position: absolute; }
  .arrow path { fill: none; stroke-linecap: round; stroke-linejoin: round; }

  .about-band { position: absolute; top: 977px; left: 0; width: 295px; height: 546px; background: var(--mist); }
  .portrait { position: absolute; top: 1037px; left: 74px; width: 358px; height: 406px;
    border: 2px solid #cfcfcf; background: linear-gradient(180deg, #f4f4f4 0%, #e9e6e3 60%, #f7f7f7 100%); }

  .section-title { position: absolute; font-family: "Jost", sans-serif; font-weight: 300;
    font-size: 55px; line-height: 1; color: var(--ink); letter-spacing: .5px; white-space: nowrap; }
  .title-rule { position: absolute; height: 1px; background: var(--rule); }
  .title-rule::after { content: ""; position: absolute; left: 50%; top: -1px; width: 28px; height: 2px;
    margin-left: -14px; background: var(--accent); }

  .about-copy { position: absolute; top: 1135px; left: 480px; width: 640px;
    font-size: 20px; line-height: 28px; color: var(--ink); }
  .about-copy p + p { margin-top: 14px; }

  .gallery-shadow { position: absolute; top: 1685px; left: 159px; width: 916px; height: 546px; background: var(--shadow); }
  .gallery-piece { position: absolute; top: 1669px; left: 133px; width: 929px; height: 546px;
    background:
      radial-gradient(ellipse at 20% 20%, rgba(200,100,30,.9), transparent 45%),
      radial-gradient(ellipse at 45% 30%, rgba(30,140,150,.85), transparent 40%),
      radial-gradient(ellipse at 65% 65%, rgba(30,30,30,.9), transparent 45%),
      radial-gradient(ellipse at 85% 30%, rgba(240,235,225,.9), transparent 40%),
      radial-gradient(ellipse at 20% 85%, rgba(40,130,100,.8), transparent 45%),
      linear-gradient(135deg, #b8692a, #2f8f8c 45%, #2a2a2a 65%, #c9a24a); }

  .contact-intro { position: absolute; top: 2452px; left: 0; width: 1200px; text-align: center; font-size: 21px; color: var(--ink); }
  .contact-list { position: absolute; top: 2519px; left: 0; width: 1200px; list-style: none; font-size: 17px; color: var(--accent); }
  .contact-list li { position: absolute; left: 0; width: 1200px; display: flex; justify-content: center; align-items: center; gap: 8px; }
  .contact-list svg { flex: none; }
  .social-dot { width: 22px; height: 22px; border: 1.5px solid var(--ink); border-radius: 50%; }

  .footer-rule { position: absolute; top: 2822px; left: 98px; width: 1004px; height: 1px; background: var(--rule); }
  .footer-note { position: absolute; top: 2850px; left: 0; width: 1200px; text-align: center; font-size: 14px; color: var(--ink); }
</style>
</head>
<body>
  <header>
    <div class="brand"><span>LYDIA</span><span class="brand-mark"></span><span>MARROW</span></div>
    <div class="header-rule"></div>
    <nav class="main-nav">
      <a href="#home" style="left:303px">HOME</a>
      <span class="nav-dot" style="left:377px"></span>
      <a href="#about" style="left:491px">ABOUT ME</a>
      <span class="nav-dot" style="left:591px"></span>
      <a href="#gallery" style="left:690px">GALLERY</a>
      <span class="nav-dot" style="left:795px"></span>
      <a href="#contact" style="left:886px">CONTACT</a>
    </nav>
  </header>

  <section id="home">
    <div class="hero" role="img" aria-label="Featured abstract painting in greens, teal and ochre brushstrokes"></div>
    <svg class="arrow" style="left:22px;top:468px" width="30" height="48" viewBox="0 0 30 48"><path d="M24 4 L6 24 L24 44" stroke="#ffffff" stroke-width="3"/></svg>
    <svg class="arrow" style="left:1134px;top:468px" width="30" height="48" viewBox="0 0 30 48"><path d="M6 4 L24 24 L6 44" stroke="#ffffff" stroke-width="3"/></svg>
  </section>

  <section id="about">
    <div class="about-band"></div>
    <div class="portrait" role="img" aria-label="Artist headshot"></div>
    <h2 class="section-title" style="left:480px;top:1044px">ABOUT ME</h2>
    <div class="title-rule" style="left:480px;top:1107px;width:253px"></div>
    <div class="about-copy">
      <p>Lorem ipsum dolor sit amet, consectetur adipiscing elit, sed do eiusmod tempor incididunt ut labore et dolore magna aliqua. Ut enim ad minim veniam, quis nostrud exercitation Lorem ipsum dolor sit amet, consect­etur adipiscing elit, sed do eiusmod tempor</p>
      <p>Duis aute irure dolor in reprehenderit in voluptate velit esse cillum dolore eu fugiat nulla pariatur. Excepteur sint occaecat cupidatat non proident, sunt in culpa qui officia deserunt mollit anim id est laborum.</p>
      <p>Sed ut perspiciatis unde pariatur. Excepteur sint occaecat cupidatat non proident, sunt in culpa qui officia deserunt mollit</p>
    </div>
  </section>

  <section id="gallery">
    <h2 class="section-title" style="left:0;width:1200px;text-align:center;top:1566px">GALLERY</h2>
    <div class="title-rule" style="left:504px;top:1629px;width:190px"></div>
    <div class="gallery-shadow"></div>
    <div class="gallery-piece" role="img" aria-label="Abstract painting in burnt orange, teal, black and white strokes"></div>
    <svg class="arrow" style="left:50px;top:1912px" width="34" height="54" viewBox="0 0 34 54"><path d="M28 4 L6 27 L28 50" stroke="#555555" stroke-width="3.5"/></svg>
    <svg class="arrow" style="left:1117px;top:1912px" width="34" height="54" viewBox="0 0 34 54"><path d="M6 4 L28 27 L6 50" stroke="#555555" stroke-width="3.5"/></svg>
  </section>

  <section id="contact">
    <h2 class="section-title" style="left:0;width:1200px;text-align:center;top:2335px">CONTACT ME</h2>
    <div class="title-rule" style="left:439px;top:2405px;width:323px"></div>
    <p class="contact-intro">Please get in touch with me on below details.</p>
    <ul class="contact-list">
      <li style="top:0">
        <svg width="28" height="20" viewBox="0 0 28 20"><rect x="1" y="1" width="26" height="18" fill="none" stroke="#3b3b3b" stroke-width="1.3"/><path d="M1 1 L14 12 L27 1 M1 19 L11 10 M27 19 L17 10" fill="none" stroke="#3b3b3b" stroke-width="1.3"/></svg>
        <span>info@lydiamarrow.com</span>
      </li>
      <li style="top:51px">
        <svg width="28" height="28" viewBox="0 0 28 28"><path d="M6 3 L10 3 L12 9 L9 11 C11 15 13 17 17 19 L19 16 L25 18 L25 22 C25 24 23 26 21 25 C12 23 5 16 3 7 C2 5 4 3 6 3 Z" fill="none" stroke="#3b3b3b" stroke-width="1.3" stroke-linejoin="round"/><path d="M16 3 C21 4 24 7 25 12 M16 7 C19 8 20 9 21 12" fill="none" stroke="#3b3b3b" stroke-width="1.2"/></svg>
        <span>Phone: (555) 014 2738</span>
      </li>
      <li style="top:100px">
        <span class="social-dot"></span>
        <span>studio @lmarrowart</span>
      </li>
      <li style="top:152px">
        <span class="social-dot"></span>
        <span>videos @lmpainter</span>
      </li>
    </ul>
  </section>

  <footer>
    <div class="footer-rule"></div>
    <p class="footer-note">© 2022 Lydia Marrow &nbsp; All Rights Reserved</p>
  </footer>
</body>
</html>
```